New Business Card for our Indoor Golf Training Facility

We are looking for designs for a new business card for our indoor golf training facility. Attached is our logo, our logo with our slogan, and here is our elevator pitch (What makes us different from the others) not sure if all the info will fit on one card, maybe you can condense the elevator pitch? here is the info

Elevator Pitch
We work with serious golfers and those that want to be serious golfers…
to make you better, faster, at all phases of the game…
We use the same state-of-the-art technology as professional golfers…
which produces data sets that shows your improvement in real time.
Our facility is available 24/7 to our members, which allows you to improve on your time.

our website: www.birchpinlinks.com

Target Market(s)

Golfers

Font styles to use
Serif
Sans Serif

Colors
ec1f27
f59195
fbd4d5
919191
d3d3d3
1b1b1b

Requirements
Must have
• our logo or our logo with the slogan, elevator pitch (can be condensed or shortened)

```html
<!DOCTYPE html>
<html lang="en">
<head>
<meta charset="utf-8">
<title>Birch Pin Links – Business Card</title>
<link href="https://fonts.googleapis.com/css2?family=Open+Sans:wght@400;600;700&family=Source+Sans+3:ital,wght@0,400;0,700;1,700&display=swap" rel="stylesheet">
<style>
  :root {
    --brand-red: #ec3b36;
    --ink: #1b1b1b;
    --rule: #919191;
    --paper: #ffffff;
    --backdrop: #5c5c5c;
  }
  * { box-sizing: border-box; margin: 0; padding: 0; }
  html, body { width: 1200px; height: 802px; overflow: hidden; }
  body {
    background: var(--backdrop);
    position: relative;
    font-family: "Open Sans", Arial, sans-serif;
  }
  .card {
    position: absolute;
    top: 238px;
    width: 545px;
    height: 325px;
    overflow: hidden;
  }
  .card-front { left: 40px; background: var(--paper); }
  .card-back { left: 615px; background: var(--brand-red); color: #fff;
    font-family: "Source Sans 3", Arial, sans-serif; text-align: center; }

  /* front */
  .brand {
    position: absolute; right: 42px; top: 78px;
    display: flex; flex-direction: column; align-items: flex-end;
  }
  .brand-name {
    color: var(--brand-red); font-weight: 700; font-size: 34px; line-height: 1.1;
  }
  .brand-slogan {
    color: var(--brand-red); font-size: 13px; line-height: 1.3; margin-top: 3px;
  }
  .person-name {
    position: absolute; left: 33px; top: 205px;
    color: var(--brand-red); font-size: 21px; font-weight: 400;
  }
  .person-title {
    position: absolute; left: 33px; top: 229px;
    color: var(--ink); font-size: 15.5px;
  }
  .title-rule {
    position: absolute; left: 176px; right: 38px; top: 238px;
    height: 1px; background: var(--rule);
  }
  .contact {
    position: absolute; left: 30px; top: 258px;
    color: var(--ink); font-size: 15.5px; line-height: 20px;
  }
  .contact-line { display: flex; align-items: center; gap: 2px; }
  .contact-line svg { width: 17px; height: 17px; flex: none; }
  .address {
    position: absolute; right: 38px; top: 258px; text-align: right;
    color: var(--ink); font-size: 15.5px; line-height: 20px; font-style: normal;
  }
  .front-band {
    position: absolute; left: 0; right: 0; bottom: 0; height: 13px;
    background: var(--brand-red);
  }

  /* back */
  .back-texture {
    position: absolute; inset: 0;
    background: radial-gradient(ellipse at center, #ee4440 0%, var(--brand-red) 70%);
  }
  .pitch-title {
    position: absolute; left: 0; right: 0; top: 60px;
    font-size: 20px; font-weight: 700; letter-spacing: 0.3px;
  }
  .pitch-body {
    position: absolute; left: 20px; right: 20px; top: 109px;
    font-size: 15px; line-height: 20px;
  }
  .pitch-body p + p { margin-top: 6px; }
  .pitch-body p:last-child { margin-top: 8px; }
  .back-rule {
    position: absolute; left: 45px; right: 45px; top: 262px;
    height: 1px; background: rgba(255,255,255,0.45);
  }
  .visit {
    position: absolute; left: 0; right: 0; top: 275px; font-size: 15px;
  }
  .visit strong { font-style: italic; font-weight: 700; font-size: 19px; }
</style>
</head>
<body>
  <section class="card card-front" aria-label="Business card front">
    <div class="brand">
      <span class="brand-name">Birch Pin Links</span>
      <span class="brand-slogan">Train Smarter. Play Sharper. Every Day.</span>
    </div>

    <h1 class="person-name">Daniel Reyes</h1>
    <p class="person-title">Managing Director</p>
    <div class="title-rule"></div>

    <div class="contact">
      <div class="contact-line">
        <svg viewBox="0 0 20 20" aria-hidden="true">
          <circle cx="10" cy="10" r="8" fill="none" stroke="var(--brand-red)" stroke-width="1.8"/>
          <path d="M7.2 5.8c-.6.5-.9 1.2-.6 2.3.6 2.2 2.9 4.6 5.1 5.2 1 .3 1.7 0 2.2-.6l-1.5-1.5-1.2.6c-1-.5-1.9-1.4-2.4-2.4l.6-1.2z" fill="var(--brand-red)"/>
        </svg>
        <span>555-210-3870</span>
      </div>
      <div class="contact-line">
        <svg viewBox="0 0 20 20" aria-hidden="true">
          <circle cx="10" cy="10" r="8" fill="var(--brand-red)"/>
          <circle cx="10" cy="10" r="4.5" fill="none" stroke="#fff" stroke-width="1.6"/>
          <path d="M5.5 10h9M10 5.5v9" stroke="#fff" stroke-width="1.2"/>
        </svg>
        <span>www.birchpinlinks.com</span>
      </div>
    </div>

    <address class="address">
      418 Meadow Crest Dr. Suite B4<br>
      Fairbrook, OH 45000
    </address>

    <div class="front-band"></div>
  </section>

  <section class="card card-back" aria-label="Business card back">
    <div class="back-texture" role="img" aria-label="Faint repeating pattern across the red background"></div>
    <h2 class="pitch-title">ELEVATOR PITCH</h2>
    <div class="pitch-body">
      <p>We work with serious golfers and those that want to be serious golfers…<br>
      to make you better, faster, at all phases of the game…</p>
      <p>We use the same state-of-the-art technology as professional golfers…<br>
      which produces data sets that shows your improvement in real time.</p>
      <p>Our facility is available 24/7 to our members, which allows<br>
      you to improve on your time.</p>
    </div>
    <div class="back-rule"></div>
    <p class="visit">Visit <strong>www.birchpinlinks.com</strong> for more details.</p>
  </section>
</body>
</html>
```